Buch-/E-Book-Cover im Bereich der Persönlichkeitsentwicklung
Vielen lieben Dank für die super Arbeit von Dir. Das Design ist klasse und die vielen Vorschläge waren auch super. Die komplette Zusammenarbeit verlief sehr professionell und Änderungswünsche wurden sehr schnell umgesetzt. Ich kann Dich voll und ganz weiterempfehlen.
Zielgruppe
Wir arbeiten in der Persönlichkeitsentwicklung für Jugendliche. Dabei spezialisieren wir uns auf den Altersbereich 12 - 17 Jahre. Unser Ziel ist es jungen Menschen zu zeigen, wie Sie zu sich selbst finden und ein glückliches sowie erfolgreiches Leben führen können.
Aufgabenstellung
- Das Design sollte für die Eltern von Teenagern und auch für die Teenager selbst ausgelegt werden. Das Buch ist für die Jugendlichen (Mädchen und Jungen im Alter zwischen 12 Jahren und 17 Jahren) gedacht, wird allerdings meist von deren Mütter gekauft.
- Der Name des Autors lautet: Henrik Falbe
- Der Titel lautet: Junge Herzen finden Mut und Richtung
- Der Untertitel lautet: Was Heranwachsende über ihren Weg lernen
- Im Anhang befinden sich Designs, die ich gut finde (nur falls jemand weitere Ideen haben möchte)
- Format: 15,24 cm x 22,86 cm (6' x 9') [genaue Maße fürs Taschenbuch und Hardcover sind im Anhang (.zip Dateien)]
1. E-Book:
- Coverdateien sollten idealerweise 2 560 Pixel hoch und 1 600 Pixel breit sein. Zur Gewährleistung der bestmöglichen Qualität (insbesondere auf HD-Geräten) sollte das Bild mindestens 2 500 Pixel hoch sein.
- Format: TIFF (.tif/.tiff) oder JPEG (.jpeg/.jpg)
- DPI: 72 dpi
- Größe: Ihr Coverbild muss kleiner als 50 MB sein.
Hinweis: Vermeiden Sie es, Ihre Dateien zu komprimieren. Dies kann die Qualität Ihres Covers auf Lesegeräten beeinträchtigen. Das beste Ergebnis erzielen Sie mit Bildern, die eine Mindestauflösung von 300 ppi (Pixels per Inch) haben.
- Rahmen: Coverbilder mit weißem oder sehr hellem Hintergrund heben sich kaum vom weißen Hintergrund ab. Fügen Sie einen dünnen Rahmen (3–4 Pixel) in Mittelgrau hinzu, um die Ränder des Covers besser sichtbar zu machen.
2. + 3. Taschenbuch/Hardcover [genaue Maße fürs Taschenbuch und Hardcover sind im Anhang (.zip Dateien)] :
- Dateityp: Das Cover muss als einzelne PDF-Datei vorliegen und die hintere Coverseite, den Buchrücken und die vordere Coverseite als einzelnes Bild enthalten.
- Dateigröße: Coverdateien, die größer als 650 MB sind, können nicht konvertiert werden. Die Datei sollte maximal 40 MB groß sein, da sich bei großen Dateien der Druck verlangsamt.
- Die gen..

```html
<!DOCTYPE html>
<html lang="de">
<head>
<meta charset="utf-8">
<title>Junge Herzen finden Mut und Richtung – Henrik Falbe</title>
<link href="https://fonts.googleapis.com/css2?family=Rubik+Dirt&family=Pompiere&family=Oswald:wght@500&display=swap" rel="stylesheet">
<style>
  :root {
    --page: #ffffff;
    --cover: #14adc8;
    --ink-light: #ffffff;
    --ink-dark: #1b1b1b;
    --frame: #9a9a9a;
    --figure-tone: #2f8fa3;
  }
  html, body {
    margin: 0;
    padding: 0;
    width: 871px;
    height: 1200px;
    overflow: hidden;
    background: var(--page);
  }
  .canvas {
    position: relative;
    width: 871px;
    height: 1200px;
  }
  .cover {
    position: absolute;
    left: 84px;
    top: 73px;
    width: 705px;
    height: 1055px;
    background: var(--cover);
    outline: 1px solid var(--frame);
    overflow: hidden;
  }
  .author {
    position: absolute;
    left: 0;
    right: 0;
    top: 112px;
    text-align: center;
    font-family: "Oswald", sans-serif;
    font-weight: 500;
    font-size: 25px;
    letter-spacing: 1px;
    color: var(--ink-light);
    margin: 0;
  }
  .title { margin: 0; }
  .title span { position: absolute; white-space: nowrap; line-height: 1; }
  .title-big {
    font-family: "Rubik Dirt", system-ui, sans-serif;
    color: var(--ink-light);
  }
  .title-small {
    font-family: "Pompiere", cursive;
    color: var(--ink-dark);
  }
  .t-line1 { left: 0; right: 0; text-align: center; top: 150px; font-size: 72px; }
  .t-line2 { left: 0; right: 0; text-align: center; top: 236px; font-size: 64px; }
  .t-line3 { left: 0; right: 0; text-align: center; top: 284px; font-size: 200px; }
  .t-line4 { left: 188px; top: 494px; font-size: 64px; }
  .t-line5 { left: 270px; top: 484px; font-size: 80px; }
  .subtitle {
    position: absolute;
    left: 392px;
    top: 670px;
    margin: 0;
    font-family: "Pompiere", cursive;
    font-size: 42px;
    line-height: 47px;
    text-transform: uppercase;
    color: var(--ink-light);
  }
  .decor { position: absolute; left: 0; top: 0; }
  .hero-figure {
    position: absolute;
    left: 234px;
    top: 702px;
    width: 160px;
    height: 353px;
    background: linear-gradient(180deg, rgba(47,143,163,0.35), var(--figure-tone));
    border-radius: 6px 6px 0 0;
  }
</style>
</head>
<body>
<div class="canvas">
  <div class="cover">
    <p class="author">HENRIK FALBE</p>

    <h1 class="title">
      <span class="title-big t-line1">Junge Herzen</span>
      <span class="title-small t-line2">finden</span>
      <span class="title-big t-line3">Mut</span>
      <span class="title-small t-line4">und</span>
      <span class="title-big t-line5">Richtung</span>
    </h1>

    <svg class="decor" width="705" height="1055" viewBox="0 0 705 1055" aria-hidden="true">
      <g fill="var(--ink-light)">
        <polygon class="star" points="323,637 329,652 345,652 332,662 337,677 323,668 309,677 314,662 301,652 317,652"/>
        <path class="cloud" d="M186,702 h40 a10,10 0 0 0 0,-20 a12,12 0 0 0 -20,-8 a14,14 0 0 0 -24,8 a10,10 0 0 0 4,20 z"/>
        <path class="cloud" d="M86,904 h40 a10,10 0 0 0 0,-20 a12,12 0 0 0 -20,-8 a14,14 0 0 0 -24,8 a10,10 0 0 0 4,20 z"/>
        <path class="cloud" d="M440,876 h40 a10,10 0 0 0 0,-20 a12,12 0 0 0 -20,-8 a14,14 0 0 0 -24,8 a10,10 0 0 0 4,20 z"/>
        <path class="cloud" d="M496,1020 h60 a14,14 0 0 0 0,-28 a16,16 0 0 0 -28,-12 a20,20 0 0 0 -34,12 a14,14 0 0 0 2,28 z"/>
      </g>
    </svg>

    <div class="hero-figure" role="img" aria-label="Illustration: eine junge Heldin mit rotem Umhang klettert auf einen Bücherstapel und greift nach einem Stern"></div>

    <p class="subtitle">Was Heranwachsende<br>über ihren<br>Weg lernen</p>
  </div>
</div>
</body>
</html>
```